Card design for orthopaedic surgeons working as The Brightwater Joint Centre

Business cards, letterhead

Colors

Designer to choose colors to be used in the design.

Requirements
Must have
• Late addition.
• Cards letterhead must have logos of
• Crestmoor Lindell College of Surgeons
• Varenwood Bone Health Association
Nice to have
• Back of card to have space for appointment time to be added by hand and some blank space for writing incidental other notes.

```html
<!DOCTYPE html>
<html lang="en">
<head>
<meta charset="utf-8">
<title>The Brightwater Joint Centre — Stationery</title>
<link href="https://fonts.googleapis.com/css2?family=Montserrat:wght@500&family=Lato:wght@400;700&family=Roboto:wght@400&display=swap" rel="stylesheet">
<style>
  :root{
    --navy:#0b3350;
    --sky:#45a2dc;
    --ink:#1d2a3a;
    --paper:#ffffff;
    --backdrop:#e7e5e2;
    --crest:#c9a25a;
    --grey:#6f6f6f;
  }
  *{margin:0;padding:0;box-sizing:border-box}
  html,body{width:1200px;height:1200px;overflow:hidden;background:var(--backdrop)}
  .canvas{position:relative;width:1200px;height:1200px}
  .sheet{position:absolute;background:var(--paper);box-shadow:0 4px 14px rgba(0,0,0,.18);overflow:hidden}
  .letterhead{left:14px;top:95px;width:785px;height:1009px}
  .wave{position:absolute;left:0;top:0}
  .brand{position:absolute;font-family:"Montserrat",sans-serif;font-weight:500;color:var(--sky);white-space:nowrap;letter-spacing:-.3px}
  .letterhead .brand{left:64px;top:88px;font-size:30px}
  .contact-list{position:absolute;list-style:none;font-family:"Roboto",sans-serif;color:#fff}
  .letterhead .contact-list{left:58px;top:918px;font-size:13px;line-height:16px}
  .contact-list li{display:flex;align-items:center;gap:8px}
  .contact-list svg{width:10px;height:10px;fill:var(--sky);flex:none}
  .badge{position:absolute;display:flex;flex-direction:column;align-items:center;text-align:center}
  .badge .mark{border-radius:6px}
  .badge .caption{font-family:"Lato",sans-serif;line-height:1.15;margin-top:4px}
  .badge--assoc .mark{background:linear-gradient(#d9b46a,#8c7a5c)}
  .badge--college .mark{background:linear-gradient(#e0b25a,#b8433a 60%,#6c8a5a)}
  .letterhead .badge--assoc{left:486px;top:835px;width:116px}
  .letterhead .badge--assoc .mark{width:54px;height:54px}
  .letterhead .badge--assoc .caption{font-size:9px;color:var(--grey)}
  .letterhead .badge--college{left:620px;top:803px;width:118px}
  .letterhead .badge--college .mark{width:92px;height:112px}
  .letterhead .badge--college .caption{font-size:7px;color:#222;font-weight:700}
  .caption b{color:var(--sky);font-weight:700;display:block;font-size:11px;color:var(--grey)}
  .caption .accent{color:#2d3f9a}

  .card{width:367px;height:212px}
  .card-front{left:819px;top:369px}
  .card-back{left:819px;top:619px}
  .card-front .brand{left:18px;top:32px;font-size:13.5px}
  .card-front .badge--assoc{left:284px;top:18px;width:66px}
  .card-front .badge--assoc .mark{width:28px;height:26px}
  .card-front .badge--assoc .caption{font-size:4.5px;color:var(--grey);margin-top:2px}
  .card-front .badge--assoc .caption b{font-size:9px}
  .card-front .badge--college{left:286px;top:82px;width:62px}
  .card-front .badge--college .mark{width:40px;height:48px;border-radius:4px}
  .card-front .badge--college .caption{font-size:3.5px;color:#222;margin-top:2px}
  .holder{position:absolute;left:18px;top:102px;font-family:"Lato",sans-serif;color:#fff;font-size:9px;line-height:12px}
  .holder .name{color:var(--sky);font-weight:700;font-size:11.5px;line-height:14px}
  .holder .role{margin-bottom:6px}
  .holder .address{margin-bottom:5px}
  .card-front .contact-list{position:static;font-family:"Lato",sans-serif;font-size:9px;line-height:12px}
  .card-front .contact-list li{gap:6px}
  .card-front .contact-list svg{width:7px;height:7px}

  .appointment{position:absolute;left:26px;top:42px;right:26px;font-family:"Lato",sans-serif;color:var(--navy);font-size:9.5px}
  .appointment h2{color:var(--sky);font-size:18px;font-weight:700;letter-spacing:.2px;margin-bottom:20px}
  .field-row{display:flex;align-items:flex-end;gap:4px;margin-bottom:8px;height:12px}
  .fill{flex:1;border-bottom:1px dotted var(--navy);height:9px}
  .fill--short{flex:0 0 88px}
  .tick{display:inline-block;width:7px;height:7px;border:1.2px solid var(--navy);margin-right:2px;vertical-align:-1px}
  .days{display:flex;justify-content:space-between;margin-bottom:20px}
  .note{color:var(--sky);font-size:9.3px}
</style>
</head>
<body>
<div class="canvas">

  <section class="sheet letterhead">
    <div class="brand">The Brightwater Joint Centre</div>

    <svg class="wave" width="785" height="1009" viewBox="0 0 785 1009">
      <path d="M0,872 C220,838 420,900 560,958 C660,996 740,992 785,956 L785,1009 L0,1009Z" fill="var(--sky)"/>
      <path d="M0,888 C220,856 420,916 560,972 C660,1006 740,1002 785,966 L785,1009 L0,1009Z" fill="#fff"/>
      <path d="M0,891 C220,860 420,920 560,976 C660,1010 740,1006 785,970 L785,1009 L0,1009Z" fill="var(--navy)"/>
    </svg>

    <ul class="contact-list">
      <li><svg viewBox="0 0 10 10"><path d="M2 0l2 2-1 1.5c.6 1.4 1.6 2.4 3 3L7.5 5.5l2 2L8 9.5C4 9 1 6 .5 2z"/></svg>(555) 014-2276</li>
      <li><svg viewBox="0 0 10 10"><path d="M0 2h10v6H0z M0 2l5 3.5L10 2" stroke="var(--navy)" stroke-width=".8"/></svg>hello@brightwaterjoint.example</li>
      <li><svg viewBox="0 0 10 10"><path d="M5 0a5 5 0 1 0 0 10A5 5 0 0 0 5 0zm0 1.2a3.8 3.8 0 1 1 0 7.6 3.8 3.8 0 0 1 0-7.6z"/><path d="M1 5h8M5 1v8" stroke="var(--sky)" stroke-width=".8"/></svg>www.brightwaterjoint.example</li>
      <li><svg viewBox="0 0 10 10"><path d="M5 0C3 0 1.5 1.5 1.5 3.5 1.5 6 5 10 5 10s3.5-4 3.5-6.5C8.5 1.5 7 0 5 0zm0 2a1.5 1.5 0 1 1 0 3 1.5 1.5 0 0 1 0-3z"/></svg>41 Larkspur Way, Brightwater, OH 45000</li>
    </ul>

    <div class="badge badge--assoc">
      <div class="mark" role="img" aria-label="Crest of the Varenwood Bone Health Association"></div>
      <div class="caption"><b>FVBHA</b>Fellow of the<br>Varenwood Bone Health Association</div>
    </div>
    <div class="badge badge--college">
      <div class="mark" role="img" aria-label="Coat of arms of the Crestmoor Lindell College of Surgeons"></div>
      <div class="caption">CRESTMOOR LINDELL COLLEGE OF SURGEONS</div>
    </div>
  </section>

  <section class="sheet card card-front">
    <svg class="wave" width="367" height="212" viewBox="0 0 367 212">
      <path d="M0,67 C90,62 160,80 220,120 C270,152 320,170 367,156 L367,212 L0,212Z" fill="var(--sky)"/>
      <path d="M0,73 C90,68 160,86 220,126 C270,158 320,174 367,160 L367,212 L0,212Z" fill="#fff"/>
      <path d="M0,75 C90,70 160,88 220,128 C270,160 320,176 367,162 L367,212 L0,212Z" fill="var(--navy)"/>
    </svg>
    <div class="brand">The Brightwater Joint Centre</div>

    <div class="badge badge--assoc">
      <div class="mark" role="img" aria-label="Crest of the Varenwood Bone Health Association"></div>
      <div class="caption"><b>FVBHA</b>Fellow of the<br>Varenwood Bone Health Association</div>
    </div>
    <div class="badge badge--college">
      <div class="mark" role="img" aria-label="Coat of arms of the Crestmoor Lindell College of Surgeons"></div>
      <div class="caption">CRESTMOOR LINDELL COLLEGE OF SURGEONS</div>
    </div>

    <div class="holder">
      <div class="name">ROWAN ELLERY</div>
      <div class="role">Owner</div>
      <div class="address">18 Harrow Lane, Elmford<br>NC 27, United States</div>
      <ul class="contact-list">
        <li><svg viewBox="0 0 10 10"><path d="M2 0l2 2-1 1.5c.6 1.4 1.6 2.4 3 3L7.5 5.5l2 2L8 9.5C4 9 1 6 .5 2z"/></svg>000-000-000-000</li>
        <li><svg viewBox="0 0 10 10"><path d="M0 2h10v6H0z M0 2l5 3.5L10 2" stroke="var(--navy)" stroke-width=".8"/></svg>hello@brightwaterjoint.example</li>
        <li><svg viewBox="0 0 10 10"><path d="M5 0a5 5 0 1 0 0 10A5 5 0 0 0 5 0zm0 1.2a3.8 3.8 0 1 1 0 7.6 3.8 3.8 0 0 1 0-7.6z"/><path d="M1 5h8M5 1v8" stroke="var(--sky)" stroke-width=".8"/></svg>www.brightwaterjoint.example</li>
      </ul>
    </div>
  </section>

  <section class="sheet card card-back">
    <div class="appointment">
      <h2>APPOINTMENT</h2>
      <div class="field-row">Name: <span class="fill"></span></div>
      <div class="field-row">Time: <span class="fill fill--short"></span>
        <span><span class="tick"></span>AM</span>&nbsp;<span><span class="tick"></span>PM</span>&nbsp;&nbsp;Date: <span class="fill"></span></div>
      <div class="days">
        <span><span class="tick"></span>MON</span>
        <span><span class="tick"></span>TUES</span>
        <span><span class="tick"></span>WED</span>
        <span><span class="tick"></span>THUR</span>
        <span><span class="tick"></span>FRI</span>
        <span><span class="tick"></span>SAT</span>
      </div>
      <p class="note">If you are unable to keep your appointment, please call us within 24 hours.</p>
    </div>
  </section>

</div>
</body>
</html>
```